Lurvik.no is a new website about pedagogical entrepreneurship. It's main target group is teachers. The Nordic Bureau for Digital Schooling and the National Office for Learning and Classrooms are leading the project.

The web page is meant to show examples of how different methods of entrepreneurship can be used pedagogical in a learning environment. The page will also support the user with examples of different teaching programs and other examples of best practice.

Pedagogical entrepreneurship is not about business and men in suits. It's a method for learning. The focus in the design should be on school, education and new ways of learning.

The final product should be motivating and engaging, but at the same time governmental and serious. We are not looking for something "flashy" and corporate-looking, but a moderate, task-focused and clean design that state quality.

We need designs for three pages:
1 - frontpage
2 - subpage ("Metoder og undervisningsopplegg")
3 - subpage ("Små-TOPP i Vassbygd")

The interaction design for these three pages will be uploaded as an attachment.

We would like you to find inspiration in the following websites:
- www.skapekraft.no
- www.giellu.no
- www.brightfernlab.com
- www.zyx.no
(more will be added)

Please use the attached logo, and feel free to use this as an inspiration for the rest of the design.

Target Market(s)

Teachers

Industry/Entity Type

Education

Requirements
Must have
• * Header with: Logo. Main navigation. Utility navigation. Search box.
* Footer
Should not have
• Images of men in suits.
Very strong graphical elements that stands out too much (we want it clean).

```html
<!DOCTYPE html>
<html lang="en">
<head>
<meta charset="utf-8">
<title>Lurvik.no – Pedagogical entrepreneurship</title>
<link rel="stylesheet" href="https://fonts.googleapis.com/css2?family=Source+Sans+3:ital,wght@0,400;0,600;0,700;1,700&display=swap">
<style>
  :root {
    --page-white: #ffffff;
    --stage-top: #cbd5dc;
    --stage-mid: #7fa0b3;
    --stage-bottom: #0e4c6b;
    --footer-top: #5e8aa3;
    --footer-bottom: #0d4a69;
    --card-top: #ffffff;
    --card-bottom: #dcdde0;
    --menu-grey: #c6c7c9;
    --brand-blue: #1c8ad3;
    --heading-blue: #2a5d9b;
    --link-grey: #8a8a8a;
    --util-grey: #666a70;
    --more-blue: #6aaee2;
    --rule-grey: #c4c6c9;
    --navy: #1f2650;
    --footer-link: #a8d8f8;
    --thumb-top: #c3d1da;
    --thumb-bottom: #3c6d8a;
    --meter-light: #e2e3e5;
    --meter-dark: #a7a9ad;
  }
  * { box-sizing: border-box; margin: 0; padding: 0; }
  html, body {
    width: 1200px; height: 1117px; overflow: hidden;
    background: var(--page-white);
    font-family: "Source Sans 3", sans-serif;
  }
  .canvas { position: relative; width: 1200px; height: 1117px; }
  .stage {
    position: absolute; left: 42px; top: 51px; width: 1097px; height: 865px;
    background: linear-gradient(180deg, var(--stage-top) 0%, var(--stage-mid) 45%, var(--stage-bottom) 100%);
  }
  .site-footer {
    position: absolute; left: 42px; top: 916px; width: 1097px; height: 137px;
    background: linear-gradient(180deg, var(--footer-top) 0%, var(--footer-bottom) 45%, var(--footer-bottom) 100%);
  }
  /* brand */
  .brand { position: absolute; left: 110px; top: 82px; display: flex; align-items: center; gap: 18px; }
  .brand-mark { width: 62px; height: 62px; border-radius: 50%; background: var(--brand-blue); }
  .brand-name { font-size: 54px; font-weight: 700; color: var(--brand-blue); line-height: 1; letter-spacing: -1px; }
  .brand-tagline {
    position: absolute; left: 206px; top: 136px;
    font-size: 9.5px; font-weight: 600; color: var(--page-white);
  }
  /* side panel */
  .side-panel {
    position: absolute; left: 111px; top: 229px; width: 330px; height: 607px;
    border-radius: 19px;
    background: linear-gradient(180deg, var(--card-top) 0%, var(--card-bottom) 100%);
    box-shadow: 0 10px 22px rgba(0,0,0,.25);
  }
  .main-nav { position: absolute; left: 132px; top: 248px; list-style: none; }
  .main-nav li {
    width: 280px; height: 51px; margin-bottom: 8px;
    background: var(--menu-grey);
    box-shadow: 0 2px 3px rgba(0,0,0,.2);
    padding: 8px 0 0 59px;
    color: var(--page-white); font-size: 12.5px; line-height: 1.3; text-transform: uppercase;
  }
  .meter-placeholder {
    position: absolute; left: 199px; top: 526px; width: 120px; height: 120px;
    border-radius: 50%;
    background: radial-gradient(circle at 45% 40%, var(--meter-light) 0%, var(--meter-dark) 100%);
    border: 4px solid var(--page-white);
    box-shadow: 0 0 0 1px #d5d6d8;
  }
  .meter-caption { position: absolute; left: 174px; top: 657px; }
  .meter-question { font-size: 9.5px; color: var(--link-grey); }
  .meter-link { font-size: 13px; color: var(--navy); font-weight: 600; }
  /* content card */
  .content-card {
    position: absolute; left: 399px; top: 189px; width: 709px; height: 657px;
    border-radius: 19px;
    background: linear-gradient(180deg, var(--card-top) 0%, var(--card-bottom) 100%);
    box-shadow: 0 14px 30px rgba(0,0,0,.3);
  }
  .utility-nav { position: absolute; left: 450px; top: 208px; display: flex; gap: 24px; font-size: 12px; }
  .utility-nav a { color: var(--util-grey); text-decoration: underline; }
  .search {
    position: absolute; left: 909px; top: 208px; width: 170px; height: 21px;
    display: flex; border: 1px solid var(--rule-grey); background: var(--page-white);
  }
  .search-field { flex: 1; font-size: 11px; color: var(--link-grey); padding: 2px 6px; }
  .search-button { width: 21px; background: #c9cbce; display: flex; align-items: center; justify-content: center; }
  .intro { position: absolute; left: 450px; top: 272px; color: var(--heading-blue); }
  .intro-title { font-size: 18px; font-style: italic; font-weight: 700; }
  .intro-text { font-size: 15px; line-height: 18px; margin-top: 2px; }
  .divider { position: absolute; left: 450px; top: 363px; width: 629px; height: 1px; background: var(--rule-grey); }
  .get-started { position: absolute; left: 450px; top: 393px; font-size: 17px; font-weight: 700; color: var(--heading-blue); }
  .link-column { position: absolute; top: 425px; }
  .link-column.methods { left: 450px; }
  .link-column.plans { left: 620px; }
  .column-title { font-size: 14px; color: var(--heading-blue); text-transform: uppercase; margin-bottom: 1px; }
  .link-column ul { list-style: none; }
  .link-column li { font-size: 13px; line-height: 19.2px; color: var(--link-grey); text-decoration: underline; }
  .more { display: block; margin-top: 20px; font-size: 11px; color: var(--more-blue); text-decoration: underline; }
  .link-column.plans .more { margin-top: 39px; }
  .column-rule { position: absolute; left: 590px; top: 428px; width: 1px; height: 148px; background: var(--rule-grey); }
  .carousel-arrow { position: absolute; top: 683px; }
  .carousel-arrow.prev { left: 442px; }
  .carousel-arrow.next { left: 1028px; }
  .teaser { position: absolute; top: 649px; width: 103px; text-align: center; }
  .teaser-image { width: 103px; height: 103px; background: linear-gradient(180deg, var(--thumb-top), var(--thumb-bottom)); }
  .teaser-label { margin-top: 6px; font-size: 13.5px; color: var(--link-grey); text-decoration: underline; }
  /* footer content */
  .footer-mark { position: absolute; left: 135px; top: 942px; width: 72px; height: 72px; border-radius: 50%; background: var(--brand-blue); }
  .footer-group { position: absolute; font-size: 9.5px; line-height: 13px; }
  .footer-group h4 { color: var(--page-white); font-weight: 700; font-size: 9.5px; }
  .footer-group p { color: var(--footer-link); margin-bottom: 9px; }
  .footer-group p b { color: var(--page-white); }
</style>
</head>
<body>
<div class="canvas">
  <div class="stage"></div>

  <header>
    <div class="brand">
      <span class="brand-mark"></span>
      <span class="brand-name">Lurvik</span>
    </div>
    <p class="brand-tagline">Entreprenerielle metoder i undervisningen</p>
  </header>

  <aside class="side-panel"></aside>
  <ul class="main-nav">
    <li>What is pedagogical<br>entrepreneurship</li>
    <li>Methods and<br>teaching plans</li>
    <li>Good examples/<br>best pratice</li>
  </ul>

  <div class="meter-placeholder" role="img" aria-label="Lurvikmeter gauge illustration"></div>
  <div class="meter-caption">
    <p class="meter-question">Are you working entrepreneurship-like?</p>
    <p class="meter-link">Try the lurvikmeter</p>
  </div>

  <main class="content-card"></main>
  <nav class="utility-nav">
    <a>best pratice school</a>
    <a>Try lurvikmeter</a>
    <a>about&nbsp; lurvik.no</a>
  </nav>
  <div class="search">
    <span class="search-field">search ...</span>
    <span class="search-button">
      <svg width="13" height="13" viewBox="0 0 13 13"><circle cx="5.5" cy="5.5" r="4" fill="none" stroke="#fff" stroke-width="1.6"/><line x1="8.5" y1="8.5" x2="12" y2="12" stroke="#fff" stroke-width="1.8"/></svg>
    </span>
  </div>

  <section class="intro">
    <h1 class="intro-title">Pedagogical entrepreneurship works.</h1>
    <p class="intro-text">Lorem ipsum dolor sit amet, consectetur adipisicing elit,<br>sed fo eiusmod tempor incididunt ut labore<br>et dolore magna aliqua.</p>
  </section>
  <div class="divider"></div>

  <h2 class="get-started">GET STARTED!</h2>
  <div class="link-column methods">
    <h3 class="column-title">Methods</h3>
    <ul>
      <li>Café-pedagogikk</li>
      <li>elevbedrift</li>
      <li>Gründercamp</li>
      <li>Story line</li>
      <li>TOPP</li>
    </ul>
    <a class="more">more...</a>
  </div>
  <div class="column-rule"></div>
  <div class="link-column plans">
    <h3 class="column-title">Teaching plans</h3>
    <ul>
      <li>Lorem Ipsum</li>
      <li>Lorem Ipsum</li>
      <li>Lorem Ipsum</li>
      <li>Lorem Ipsum</li>
    </ul>
    <a class="more">more...</a>
  </div>

  <svg class="carousel-arrow prev" width="18" height="36" viewBox="0 0 18 36"><polyline points="15,2 3,18 15,34" fill="none" stroke="#b7b9bc" stroke-width="2"/></svg>
  <div class="teaser" style="left:517px"><div class="teaser-image" role="img" aria-label="Teaser photo"></div><p class="teaser-label">Lorem ipsum</p></div>
  <div class="teaser" style="left:694px"><div class="teaser-image" role="img" aria-label="Teaser photo"></div><p class="teaser-label">Lorem ipsum</p></div>
  <div class="teaser" style="left:871px"><div class="teaser-image" role="img" aria-label="Teaser photo"></div><p class="teaser-label">Lorem ipsum</p></div>
  <svg class="carousel-arrow next" width="18" height="36" viewBox="0 0 18 36"><polyline points="3,2 15,18 3,34" fill="none" stroke="#b7b9bc" stroke-width="2"/></svg>

  <footer class="site-footer"></footer>
  <span class="footer-mark"></span>
  <div class="footer-group" style="left:254px; top:944px">
    <h4>Pedagogical entrepreneurship</h4>
    <p>What is pedagogical entrepreneurship? &nbsp;|&nbsp; Science &nbsp;|&nbsp; Best pratice schools &nbsp;|&nbsp; Lurvikmeteret &nbsp;|&nbsp; About lurvik.no</p>
    <h4>Gode eksempler</h4>
    <p>Små-TOPP at Vassbygd school &nbsp;|&nbsp; Små-TOPP at Vassbygd school &nbsp;|&nbsp; Små-TOPP at Vassbygd school &nbsp;|&nbsp; more...</p>
  </div>
  <div class="footer-group" style="left:753px; top:944px">
    <h4>Teaching Plans</h4>
    <p>Lorem Ipsum &nbsp;|&nbsp; Lorem Ipsum &nbsp;|&nbsp; Lorem Ipsum &nbsp;|&nbsp; Lorem Ipsum &nbsp;|&nbsp; more...</p>
    <h4>Methods</h4>
    <p>Story line &nbsp;|&nbsp; <b>TOPP</b> &nbsp;|&nbsp; Café-pedagogikk &nbsp;|&nbsp; more...</p>
  </div>
</div>
</body>
</html>
```